Brindle Sky Port needs a new upscale business card design for our high end aircraft hangar complex

Brindle Sky Port (BSP) is a large, upscale jet hangar complex in the US housing expensive aircraft. We need a new business card design, using our current logo. We will be attending a industry convention and need a card design that will stand out and be remembered by aircraft owners and private pilots.

Target Market(s)

Aircraft pilots or owners looking for a new upscale hangar

Industry/Entity Type

Airport

Contact Information for Business Card

I like to use very heavy card stock, 400#, double sided. Square, no rounded edges please.

Colors
3276b5
0255a3
85abd2

Requirements
Must have
• An expensive, classy design, vivid colors.
Nice to have
• Needs to look very expensive and classy, and have some "pop". Designer must be able to download or copy my current typeface or fonts.
• One card side might be black with the "Logo and Brindle Sky Port Double line image in blue (or try gold, or glossy black), and perhaps have a grayed out "K720 jet silhouette". The other card side would have our contact info, and perhaps the "BSP Logo only". I'd like my contact info 'stacked', not in a paragraph format.
Should not have
• Should not look "too busy". Having a double-sided card will help.

```html
<!DOCTYPE html>
<html lang="en">
<head>
<meta charset="utf-8">
<title>Brindle Sky Port – Business Card</title>
<link rel="stylesheet" href="https://fonts.googleapis.com/css2?family=Open+Sans:wght@400;600;700&display=swap">
<style>
  :root {
    --backdrop: #e9e7e4;
    --card: #1f2a34;
    --brand-blue: #2f97dd;
    --text-light: #f2f4f6;
    --text-soft: #dfe4e8;
  }
  * { margin: 0; padding: 0; box-sizing: border-box; }
  html, body {
    width: 1200px; height: 900px; overflow: hidden;
    background: var(--backdrop);
    font-family: "Open Sans", Arial, sans-serif;
  }
  .canvas { position: relative; width: 1200px; height: 900px; }
  .card {
    position: absolute;
    background: var(--card);
  }
  .card--contact { left: 238px; top: 62px; width: 555px; height: 342px; }
  .card--brand { left: 457px; top: 518px; width: 560px; height: 343px; }

  .brand {
    position: absolute;
    display: flex; flex-direction: column; align-items: center;
    transform: translateX(-50%);
  }
  .brand__mark {
    border-radius: 50%;
    background: var(--brand-blue);
  }
  .brand__name {
    color: var(--brand-blue);
    font-weight: 700;
    white-space: nowrap;
    line-height: 1.1;
  }
  .card--contact .brand { left: 162px; top: 118px; }
  .card--contact .brand__mark { width: 58px; height: 58px; margin-bottom: 12px; }
  .card--contact .brand__name { font-size: 27px; }
  .card--brand .brand { left: 280px; top: 104px; }
  .card--brand .brand__mark { width: 70px; height: 70px; margin-bottom: 14px; }
  .card--brand .brand__name { font-size: 33px; }

  .contact {
    position: absolute; left: 317px; top: 66px;
    color: var(--text-soft);
  }
  .contact__name { font-size: 20px; font-weight: 600; color: var(--text-light); line-height: 26px; }
  .contact__title { font-size: 15px; line-height: 20px; }
  .contact__address { margin-top: 12px; font-size: 15px; line-height: 21px; }
  .contact__list { list-style: none; margin-top: 17px; }
  .contact__item {
    display: flex; align-items: center; gap: 9px;
    font-size: 15px; line-height: 23px;
  }
  .contact__icon { width: 11px; height: 11px; fill: var(--text-light); flex: none; }
</style>
</head>
<body>
<div class="canvas">

  <section class="card card--contact">
    <div class="brand">
      <div class="brand__mark"></div>
      <div class="brand__name">Brindle Sky Port</div>
    </div>
    <div class="contact">
      <div class="contact__name">Daniel Harrow</div>
      <div class="contact__title">Managing Director</div>
      <div class="contact__address">12345, Address Goes Here<br>Country Name, 123456.</div>
      <ul class="contact__list">
        <li class="contact__item">
          <svg class="contact__icon" viewBox="0 0 12 12"><path d="M2.5 0.5 L4.5 0.5 L5.3 3 L4 4.2 Q5 6.6 7.8 8 L9 6.7 L11.5 7.5 L11.5 9.5 Q11.5 11.5 9.5 11.5 Q0.5 10.5 0.5 2.5 Q0.5 0.5 2.5 0.5Z"/></svg>
          (044)-555-0142
        </li>
        <li class="contact__item">
          <svg class="contact__icon" viewBox="0 0 12 12"><rect x="1" y="3" width="10" height="8" rx="1"/><rect x="3" y="0.5" width="6" height="3" fill="none" stroke="#f2f4f6" stroke-width="1.2"/><rect x="3" y="6" width="6" height="1" fill="#1f2a34"/></svg>
          123-555-0178
        </li>
        <li class="contact__item">
          <svg class="contact__icon" viewBox="0 0 12 12"><rect x="0.5" y="2" width="11" height="8"/><path d="M0.5 2 L6 6.5 L11.5 2" fill="none" stroke="#1f2a34" stroke-width="1.2"/></svg>
          info@brindleskyport.com
        </li>
        <li class="contact__item">
          <svg class="contact__icon" viewBox="0 0 12 12"><circle cx="6" cy="6" r="5.5"/><path d="M3 3.5 Q5 4 4.5 6 Q6.5 7 5.5 10 M7.5 1.5 Q7 3.5 9 4 Q10.5 5.5 9.5 7.5" fill="none" stroke="#1f2a34" stroke-width="1"/></svg>
          www.brindleskyport.com
        </li>
      </ul>
    </div>
  </section>

  <section class="card card--brand">
    <div class="brand">
      <div class="brand__mark"></div>
      <div class="brand__name">Brindle Sky Port</div>
    </div>
  </section>

</div>
</body>
</html>
```